Business Card Re-Design/Update

We'd like to update out business cards. I've included our current "Style guide" which has the colour scheme of the organisation in it. I've also included the branding files with logos etc in them.

I've also included a copy of one of our existing cards so that you can see how ugly/dated they look. I'd like a fresh modern corporate look.

Target Market(s)

These are for our clients, potential clients, industry contacts - like all business cards

Contact Information for Business Card

Name
Position
Company Address - Level 1, 47 Fernby Street, Carlow Qld 4072
Direct Phone
mobile
Email
Website -www.korvalit.com.au
Logo

Colors

Designer to choose colors to be used in the design.

Requirements
Must have
• Main Logo
• Cards will need to be editable to be able to personalize them for each new employee.
Nice to have
• The MapOut, ShipWell, KeepSteady would be okay to have if they can be sensibly and professionally added to the look without detracting from the main imagery.
• Maybe they could go on the back of the card? will leave this to your creative discretion as to whether/where they fit.
Should not have
• Should not have decorative or script fonts

```html
<!DOCTYPE html>
<html lang="en">
<head>
<meta charset="utf-8">
<title>korvalIT business card</title>
<link rel="stylesheet" href="https://fonts.googleapis.com/css2?family=Montserrat:wght@400;500;600;700&family=Roboto+Condensed:wght@700&display=swap">
<style>
  :root {
    --brand-red: #d71f27;
    --deep-red: #a9171d;
    --ink: #3a3a3c;
    --paper: #ffffff;
    --backdrop: #2a0a0b;
    --soft-white: #f4e9ea;
  }
  * { box-sizing: border-box; margin: 0; padding: 0; }
  html, body { width: 1200px; height: 1200px; overflow: hidden; }
  body {
    background: var(--backdrop);
    font-family: "Montserrat", sans-serif;
    display: flex;
    flex-direction: column;
    align-items: center;
    justify-content: center;
    gap: 60px;
  }
  .card {
    position: relative;
    width: 900px;
    height: 514px;
    overflow: hidden;
    box-shadow: 0 18px 40px rgba(0,0,0,.45);
  }

  /* Front */
  .card-front { background: var(--paper); color: var(--ink); }
  .front-brand {
    position: absolute; top: 82px; left: 300px;
    display: flex; align-items: center; gap: 22px;
  }
  .brand-square { width: 46px; height: 46px; background: var(--brand-red); }
  .brand-name { font-size: 66px; font-weight: 600; color: var(--ink); letter-spacing: -0.5px; line-height: 1; }
  .name-band {
    position: absolute; top: 206px; left: 0; right: 0; height: 60px;
    background: linear-gradient(90deg, var(--deep-red), var(--brand-red));
    display: flex; align-items: center; padding-left: 120px; color: var(--paper);
  }
  .person-name { font-size: 28px; font-weight: 600; letter-spacing: .5px; }
  .band-divider { width: 2px; height: 24px; background: var(--paper); margin: 0 18px; }
  .person-role { font-size: 16px; font-weight: 500; }
  .address {
    position: absolute; top: 300px; right: 60px;
    font-size: 17px; font-weight: 500;
  }
  .rule {
    position: absolute; top: 336px; left: 120px; right: 60px; height: 1px;
    background: linear-gradient(90deg, rgba(215,31,39,0), var(--brand-red) 40%, rgba(215,31,39,0));
  }
  .contacts {
    position: absolute; top: 370px; left: 60px; right: 40px;
    display: flex; font-size: 17px; font-weight: 500; line-height: 1.55;
  }
  .contact-group { padding: 0 22px; border-left: 2px solid var(--brand-red); }
  .contact-group:first-child { border-left: none; padding-left: 0; }
  .label { color: var(--brand-red); font-weight: 700; display: inline-block; width: 20px; }

  /* Back */
  .card-back {
    background: linear-gradient(160deg, #c91d24 0%, var(--brand-red) 45%, var(--deep-red) 100%);
    color: var(--paper);
  }
  .back-texture { position: absolute; inset: 0; }
  .back-brand {
    position: absolute; top: 190px; left: 110px;
    font-size: 68px; font-weight: 600; letter-spacing: -0.5px; color: var(--paper);
  }
  .service-list {
    position: absolute; top: 300px; left: 90px;
    display: flex; gap: 24px; list-style: none;
  }
  .service {
    width: 104px; height: 104px; border: 2px solid var(--paper); border-radius: 50%;
    display: flex; align-items: center; justify-content: center; text-align: center;
    font-family: "Roboto Condensed", sans-serif; font-weight: 700; font-size: 19px; line-height: 1.1;
  }
</style>
</head>
<body>
  <section class="card card-front" aria-label="Card front">
    <div class="front-brand">
      <span class="brand-square"></span>
      <span class="brand-name">korvalIT</span>
    </div>
    <div class="name-band">
      <span class="person-name">Mara Doyle</span>
      <span class="band-divider"></span>
      <span class="person-role">Business Development Manager</span>
    </div>
    <p class="address">Level 1, 47 Fernby Street, Carlow Qld 4072</p>
    <div class="rule"></div>
    <div class="contacts">
      <div class="contact-group">
        <div><span class="label">M</span>+61 (0)400 555 118</div>
        <div><span class="label">P</span>+61 (0)7 3000 4410</div>
      </div>
      <div class="contact-group">
        <div><span class="label">D</span>+61 (0)7 3000 4426</div>
        <div><span class="label">F</span>+61 (0)7 3000 4402</div>
      </div>
      <div class="contact-group">
        <div><span class="label">E</span>mdoyle@korvalit.com.au</div>
        <div><span class="label">W</span>www.korvalit.com.au</div>
      </div>
    </div>
  </section>

  <section class="card card-back" aria-label="Card back">
    <svg class="back-texture" width="900" height="514" viewBox="0 0 900 514" role="img" aria-label="Soft faceted triangle texture in red and pale pink">
      <defs>
        <linearGradient id="paleFacet" x1="0" y1="1" x2="1" y2="0">
          <stop offset="0" stop-color="#f7f1f2"/>
          <stop offset="1" stop-color="#e9b9bd"/>
        </linearGradient>
      </defs>
      <polygon points="560,514 900,150 900,514" fill="url(#paleFacet)"/>
    </svg>
    <div class="back-brand">korvalIT</div>
    <ul class="service-list">
      <li class="service">The<br>MapOut</li>
      <li class="service">ShipWell</li>
      <li class="service">Keep<br>Steady</li>
    </ul>
  </section>
</body>
</html>
```